Redesign of LumoWordfind.com in Bootstrap 4

Current design of LumoWordfind.com is not responsive. We need to change it to latest version of Bootstrap 4 keeping essential elements in place.

Apart from home page, we need designs for http://www.lumowordfind.com/meaning/cat also.

Coding

Number of Pages Required

2 page

Colors
34a7d8

Requirements
Must have
• Bootstrap 4

```html
<!DOCTYPE html>
<html lang="en">
<head>
<meta charset="utf-8">
<title>Lumo Wordfind – Home</title>
<link rel="stylesheet" href="https://fonts.googleapis.com/css2?family=Roboto:wght@400;500;700&family=Open+Sans:wght@400;600&family=Montserrat:wght@600;700;800&display=swap">
<style>
:root{
  --brand:#34a7d8;
  --brand-dark:#2a93c4;
  --heading:#2b9fd3;
  --orange:#f7941d;
  --orange-bright:#ff9c12;
  --hero-a:#44b7cc;
  --hero-b:#2a93b2;
  --ink:#333;
  --muted:#555;
  --line:#dcdcdc;
  --panel:#e9e9e9;
  --white:#fff;
}
*{box-sizing:border-box;margin:0;padding:0}
html,body{width:982px;height:1200px;overflow:hidden}
body{position:relative;background:#f2f2f2;font-family:"Roboto",sans-serif;color:var(--ink);font-size:9px}
.abs{position:absolute}

/* hero */
.hero{left:0;top:0;width:982px;height:338px;background:linear-gradient(160deg,var(--hero-a) 0%,#3aa8c4 45%,var(--hero-b) 100%);overflow:hidden}
.menu-panel{left:118px;top:0;width:137px;height:262px;background:var(--white)}
.menu-head{display:flex;align-items:center;height:48px;padding:0 14px 0 15px}
.menu-head .burger{width:21px;height:16px;display:flex;flex-direction:column;justify-content:space-between;margin-right:10px}
.menu-head .burger i{display:block;height:2px;background:var(--brand)}
.menu-head span{font-family:"Montserrat",sans-serif;font-weight:700;font-size:10px;color:var(--brand);flex:1}
.menu-list{list-style:none;padding:18px 11px 0 14px}
.menu-list li{font-size:9px;color:#444;height:31px;line-height:31px;border-bottom:1px solid #d7d7d7}
.menu-list li:first-child{height:18px;line-height:10px}
.menu-list li:last-child{border:none}
.logo-box{left:427px;top:0;width:86px;height:62px;background:#9fd6e8;display:flex;flex-direction:column;align-items:center;justify-content:center}
.logo-box b{font-family:"Montserrat",sans-serif;font-weight:800;font-size:20px;color:#222;line-height:1}
.logo-box small{font-size:9px;color:#1d6f9a;letter-spacing:.5px;margin-top:3px}
.sign-in{left:794px;top:14px;width:56px;height:27px;border:2px solid var(--orange);color:var(--orange);font-family:"Montserrat",sans-serif;font-weight:700;font-size:9px;display:flex;align-items:center;justify-content:center}
.join-tab{left:950px;top:114px;width:32px;height:116px;background:var(--orange-bright);display:flex;align-items:center;justify-content:center}
.join-tab span{transform:rotate(-90deg);white-space:nowrap;color:#fff;font-family:"Montserrat",sans-serif;font-weight:800;font-size:10px;letter-spacing:.4px}
.hero-title{left:0;top:160px;width:982px;text-align:center;font-family:"Open Sans",sans-serif;font-size:29px;color:#fff}
.search{left:273px;top:218px;width:436px;height:44px;background:rgba(40,110,130,.5);padding:3px;display:flex}
.search .field{flex:1;background:#fff;font-size:12px;color:#333;padding-left:15px;display:flex;align-items:center}
.search .btn{width:83px;background:var(--orange-bright);color:#fff;font-family:"Montserrat",sans-serif;font-weight:800;font-size:11px;letter-spacing:1.5px;display:flex;align-items:center;justify-content:center}

/* main */
.main{left:131px;top:338px;width:719px;height:698px;background:var(--white)}
.sidebar{left:139px;top:347px;width:155px;height:593px;background:var(--panel)}
.side-title{font-family:"Montserrat",sans-serif;font-weight:700;color:var(--heading);text-align:center;font-size:12px;line-height:14px}
.wotd{left:146px;top:382px;width:137px;height:124px;background:#fff;text-align:center;padding-top:19px}
.wotd h3{font-family:"Montserrat",sans-serif;font-weight:700;color:var(--orange);font-size:12px}
.wotd p{font-size:8.5px;color:#444;line-height:13.5px;margin-top:10px;padding:0 12px}
.wotd .more{font-family:"Montserrat",sans-serif;font-weight:700;font-size:7.5px;letter-spacing:1.2px;margin-top:11px;color:#333}
.ad-net{left:147px;top:518px;width:138px;height:114px;background:linear-gradient(135deg,#2b2d33,#5a4a3a 60%,#1c1d22)}
.ad-host{left:147px;top:766px;width:139px;height:114px;background:linear-gradient(160deg,#f4a533,#e07f20 55%,#2a4f9a)}
.newsletter{left:139px;top:649px;width:155px}
.email{left:149px;top:686px;width:134px;height:27px;background:#fff;border:1px solid #ccc;display:flex;align-items:center;padding-left:10px;font-size:8.5px;color:#444;gap:6px}
.signup{left:221px;top:718px;width:62px;height:22px;background:var(--orange-bright);color:#fff;font-family:"Montserrat",sans-serif;font-weight:800;font-size:9px;letter-spacing:1.5px;display:flex;align-items:center;justify-content:center}

.box{border:1px solid var(--line);background:linear-gradient(#fff,#f7f7f7)}
.features{left:302px;top:348px;width:541px;height:165px}
.features h2{position:absolute;left:22px;top:18px;font-family:"Montserrat",sans-serif;font-weight:700;color:var(--heading);font-size:13px}
.features ul{position:absolute;left:23px;top:48px;list-style:none}
.features li{display:flex;align-items:center;gap:9px;height:19.6px;font-size:8.8px;color:#444}
.features .art{position:absolute;left:338px;top:20px;width:186px;height:132px;background:radial-gradient(circle at 60% 50%,#f3d9a8,#e9b96e 50%,rgba(255,255,255,0) 72%)}

.promo{left:302px;top:524px;width:542px;height:66px;border:1px solid #222;background:#fff}
.promo .mark{position:absolute;left:15px;top:20px;width:26px;height:26px;border-radius:50%;background:#1a8fd1}
.promo .name{position:absolute;left:15px;top:49px;font-size:7px;font-weight:700;color:#1a8fd1}
.promo .msg{position:absolute;left:58px;top:17px;font-family:"Roboto",sans-serif;font-weight:700;font-size:11.5px;line-height:16px;color:#111}
.promo .cta{position:absolute;left:345px;top:22px;width:91px;height:21px;background:#e0401b;color:#fff;font-weight:700;font-size:10.5px;display:flex;align-items:center;justify-content:center}
.promo .pic{position:absolute;left:418px;top:0;width:123px;height:64px;background:linear-gradient(120deg,#f0f0f0,#c9c9c9 40%,#3b3e44 70%,#7aa0a0)}

.card{width:267px;text-align:center}
.card h3{font-family:"Montserrat",sans-serif;font-weight:700;color:var(--heading);font-size:12px;margin-top:6px}
.card p{font-size:8.8px;color:#444;line-height:14.5px}
.card .tag{display:inline-block;border:1px solid #bbb;background:#fff;font-size:8.8px;padding:0 10px;height:24px;line-height:22px;margin:12px 0 10px}
.card .go{display:inline-block;background:var(--orange-bright);color:#fff;font-family:"Montserrat",sans-serif;font-weight:700;font-size:8px;padding:0 7px;height:16px;line-height:16px;margin-top:6px;letter-spacing:.3px}
.card .icon{height:28px;margin-top:11px;display:flex;justify-content:center;align-items:center}
.c1{left:302px;top:602px;height:165px}
.c2{left:577px;top:602px;height:165px}
.c3{left:302px;top:776px;height:164px}
.c4{left:577px;top:776px;height:164px}
.c3 .icon,.c4 .icon{height:38px;margin-top:13px}
.c3 p,.c4 p{margin-top:8px}

.browse{left:141px;top:964px;width:700px;height:62px;border:1px solid var(--line)}
.browse-title{left:141px;top:958px;width:700px;text-align:center}
.browse-title span{background:#fff;padding:0 10px;font-family:"Montserrat",sans-serif;font-weight:700;font-size:9.5px;color:#555;letter-spacing:.4px}
.letters{left:181px;top:986px;display:flex;gap:4.7px}
.letters span{width:19px;height:19px;border-radius:50%;border:1px solid #ccc;background:#fafafa;box-shadow:0 1px 1px rgba(0,0,0,.15);font-size:8.5px;color:#555;display:flex;align-items:center;justify-content:center}

/* footer */
.footer{left:0;top:1036px;width:982px;height:164px;background:var(--brand);color:#fff}
.fcol{position:absolute;top:23px}
.fcol h4{font-family:"Montserrat",sans-serif;font-weight:700;font-size:9.5px;margin-bottom:13px}
.fcol a{display:block;color:#fff;text-decoration:none;font-size:7.8px;height:15.4px}
.social{display:flex;gap:8px;margin-top:3px}
.social i{width:20px;height:20px;border-radius:50%;background:#1d5f9e;display:block}
.social i.red{background:#d9262b}
.social i.light{background:#1f8fd6}
.social i.mid{background:#2a6b98}
.flogo{position:absolute;left:780px;top:22px;width:90px;text-align:center;line-height:1}
.flogo b{display:block;font-family:"Montserrat",sans-serif;font-weight:800;font-size:22px}
.flogo small{display:block;font-size:9px;letter-spacing:.5px;margin-top:2px}
.fline{position:absolute;left:131px;top:121px;width:719px;border-top:1px solid rgba(255,255,255,.35)}
.copy{position:absolute;left:131px;top:139px;font-size:7.8px}
</style>
</head>
<body>

<header class="hero abs">
  <nav class="menu-panel abs">
    <div class="menu-head">
      <div class="burger"><i></i><i></i><i></i></div>
      <span>MENU</span>
      <svg width="14" height="14" viewBox="0 0 14 14"><path d="M1 1L13 13M13 1L1 13" stroke="#34a7d8" stroke-width="1.5"/></svg>
    </div>
    <ul class="menu-list">
      <li>Home</li><li>Idioms</li><li>Common Errors</li><li>Crossword</li><li>Blog</li><li>Contact</li>
    </ul>
  </nav>
  <div class="logo-box abs"><b>Lumo</b><small>WORDFIND</small></div>
  <div class="sign-in abs">SIGN IN</div>
  <div class="join-tab abs"><span>JOIN FOR FREE</span></div>
  <h1 class="hero-title abs" style="font-weight:400">Lumo English Dictionary</h1>
  <div class="search abs"><div class="field">Enter a Word or Phrase</div><div class="btn">SEARCH</div></div>
</header>

<main class="main abs"></main>

<aside>
  <div class="sidebar abs"></div>
  <div class="side-title abs" style="left:139px;top:360px;width:155px">WORD OF THE DAY</div>
  <div class="wotd abs">
    <h3>EXHAUSTIVE</h3>
    <p>/ɪɡˈzɔːstɪv/ (s) performed comprehensively and completely</p>
    <div class="more">READ MORE</div>
  </div>
  <div class="ad-net abs" role="img" aria-label="Netoria networking advertisement with a woman holding a tablet"></div>
  <div class="newsletter abs side-title">SIGNUP FOR<br>NEWSLETTER</div>
  <div class="email abs">
    <svg width="10" height="8" viewBox="0 0 10 8"><rect x=".5" y=".5" width="9" height="7" fill="none" stroke="#555"/><path d="M.5 .5L5 4.5L9.5 .5" fill="none" stroke="#555"/></svg>
    E mail id
  </div>
  <div class="signup abs">SIGNUP</div>
  <div class="ad-host abs" role="img" aria-label="Hostwise web hosting advertisement with a cartoon mascot"></div>
</aside>

<section class="features box abs">
  <h2>SEARCH, SAVE AND MASTER WORDS</h2>
  <ul>
    <li><svg width="9" height="9" viewBox="0 0 9 9"><circle cx="4.5" cy="4.5" r="4.5" fill="#f7941d"/><path d="M2.3 4.6L3.9 6.1L6.8 3" stroke="#fff" stroke-width="1.2" fill="none"/></svg>Search from more than 300,000 words and phrases</li>
    <li><svg width="9" height="9" viewBox="0 0 9 9"><circle cx="4.5" cy="4.5" r="4.5" fill="#f7941d"/><path d="M2.3 4.6L3.9 6.1L6.8 3" stroke="#fff" stroke-width="1.2" fill="none"/></svg>Multiple usages to clarify the context</li>
    <li><svg width="9" height="9" viewBox="0 0 9 9"><circle cx="4.5" cy="4.5" r="4.5" fill="#f7941d"/><path d="M2.3 4.6L3.9 6.1L6.8 3" stroke="#fff" stroke-width="1.2" fill="none"/></svg>Audio, phonetics, meanings, synonyms and antonyms</li>
    <li><svg width="9" height="9" viewBox="0 0 9 9"><circle cx="4.5" cy="4.5" r="4.5" fill="#f7941d"/><path d="M2.3 4.6L3.9 6.1L6.8 3" stroke="#fff" stroke-width="1.2" fill="none"/></svg>Save the words to your personal deck and access from anywhere</li>
    <li><svg width="9" height="9" viewBox="0 0 9 9"><circle cx="4.5" cy="4.5" r="4.5" fill="#f7941d"/><path d="M2.3 4.6L3.9 6.1L6.8 3" stroke="#fff" stroke-width="1.2" fill="none"/></svg>It's FREE</li>
  </ul>
  <div class="art" role="img" aria-label="Illustration of an open alphabet book and a boy with a magnifying glass"></div>
</section>

<section class="promo abs">
  <div class="mark"></div>
  <div class="name">Verapoint</div>
  <div class="msg">53% of IT managers said printers were vulnerable<br>to cyber crime. What defense do you have?</div>
  <div class="pic" role="img" aria-label="Office printer and monitor product photo"></div>
  <div class="cta">Find out more</div>
</section>

<section class="card box c1 abs">
  <div class="icon"><svg width="30" height="26" viewBox="0 0 30 26"><text x="2" y="16" font-family="Georgia,serif" font-size="17" fill="#666">A</text><text x="14" y="23" font-family="Georgia,serif" font-size="15" fill="#666">b</text><path d="M0 10H30" stroke="#666" stroke-width="1.3"/></svg></div>
  <h3>ENGLISH TIDBIT</h3>
  <div class="tag">gaffe/gaff</div>
  <p><span style="color:var(--heading)">"Gaffe"</span> is a social blunder and <span style="color:var(--heading)">"gaff"</span> is a large<br>hook. Be warned not to make the gaffe of<br>mixing it up with gaff.</p>
</section>

<section class="card box c2 abs">
  <div class="icon"><svg width="25" height="25" viewBox="0 0 25 25"><rect x=".5" y=".5" width="24" height="24" fill="none" stroke="#777"/><path d="M6.5 .5V24.5M12.5 .5V24.5M18.5 .5V24.5M.5 6.5H24.5M.5 12.5H24.5M.5 18.5H24.5" stroke="#777"/><rect x="7" y="1" width="5" height="5" fill="#777"/><rect x="13" y="13" width="5" height="5" fill="#777"/><rect x="1" y="19" width="5" height="5" fill="#777"/></svg></div>
  <h3>DAILY CROSSWORD</h3>
  <div class="tag">Crossword Lovers!</div>
  <p>Take this daily crossword challenge from<br>Lumo Wordfind.</p>
  <div class="go">SOLVE NOW</div>
</section>

<section class="card box c3 abs">
  <div class="icon"><svg width="30" height="34" viewBox="0 0 30 34"><circle cx="15" cy="20" r="13" fill="#666"/><path d="M15 1V12M9.5 6.5H20.5" stroke="#666" stroke-width="1.6"/></svg></div>
  <h3>BROWSER ADDON</h3>
  <p>Add this tool to your Foxtrail Browser and quickly look<br>up for definitions from any website without<br>leaving the page.</p>
  <div class="go">GET IT NOW</div>
</section>

<section class="card box c4 abs">
  <div class="icon"><svg width="18" height="32" viewBox="0 0 18 32"><rect x="1" y="1" width="16" height="30" rx="2.5" fill="none" stroke="#666" stroke-width="1.6"/><path d="M1 5H17M1 26H17" stroke="#666" stroke-width="1.2"/><circle cx="9" cy="28.5" r="1.1" fill="#666"/></svg></div>
  <h3>DESIGNED FOR POCKETPHONE</h3>
  <p>Lumo Wordfind is specially designed for your<br>Pocketphone to quickly lookup meaining, usages and<br>audio of words.</p>
  <div class="go">GET IT NOW</div>
</section>

<section>
  <div class="browse abs"></div>
  <div class="browse-title abs"><span>BROWSE DICTIONARY</span></div>
  <div class="letters abs">
    <span>A</span><span>B</span><span>C</span><span>D</span><span>E</span><span>F</span><span>G</span><span>H</span><span>I</span><span>J</span><span>K</span><span>L</span><span>M</span><span>N</span><span>O</span><span>P</span><span>Q</span><span>R</span><span>S</span><span>T</span><span>U</span><span>V</span><span>W</span><span>X</span><span>Y</span><span>Z</span>
  </div>
</section>

<footer class="footer abs">
  <div class="fcol" style="left:131px"><h4>LUMOWORDFIND.COM</h4><a>FAQ</a><a>Contact</a><a>Blog</a></div>
  <div class="fcol" style="left:315px"><h4>LEGAL</h4><a>Privacy Policy</a><a>Terms of Use</a></div>
  <div class="fcol" style="left:455px"><h4>OTHERS</h4><a>Popular Words</a><a>Common Errors in English</a><a>Exam Prep Online</a></div>
  <div class="fcol" style="left:623px"><h4>FOLLOW US ON</h4>
    <div class="social"><i></i><i class="light"></i><i class="red"></i><i class="mid"></i></div>
  </div>
  <div class="flogo"><b>Lumo</b><small>WORDFIND</small></div>
  <div class="fline"></div>
  <div class="copy">Copyrights @ 2016 All Rights Reserved</div>
</footer>

</body>
</html>
```